Yoga/movement guide/teacher for adult yoga practice and kid yoga

What is the positioning or mission statement of your company? to guide individuals in a yoga-based safe and sustainable movement practice applicable to all ages and body types. Currently my focus is working with children in daycare and school settings, but my goal is to expand into private yoga practice for adults, and potentially as part of rented space in studios. I hope to find a way to work with children AND adults (so would love for logo to be appealing to both), but current focus is with children based on need and demand in the community. yoga for children also compliments my backround as a pediatrician/neonatologist, and I greatly miss interacting with children. I also want to emphasize a yoga/movement practice that is focused more on what one feels internally through movement. NOT what one looks like asthetically. I believe in removing all mirrors from yoga/movement practice. It should be an experience of movement/poses/yoga through appropriate cueing and education. It is not about the details of how far the knee should bend, or how high the leg should be. Focusing on foudation first, core, then core engagement and ultimately expression of poses/movements. A focus on strength, stability and mobility, not just flexibility, which is the common perception/association with yoga. I also want individuals to learn to be an advocate of their own health. Through guidance, I hope for individuals to connect with their body so they know themselves so well to be able to advocate for themselves in the modern healthcare world. This internal experience and connection is so essential in a world where modern medicine has become a business and it is all about making a dollar. the connection with patients is lost, and individuals need to learn to empower themselves and through their new found voice to be able to articulate what is wrong.<br/>Does your company have a tagline or slogan that should be included with the logo? "Practice Radiant Movement"<br/>What do you hope your company can be known for? Accessible yoga for a sustained practice. A guided movement practice where one gains information and knowledge of oneself through a mind/body connection. For one feel good physically with a new awaraness of their internal radiance that exists in all beings. Physical rejuvenation egnites a light and increases energy to flow through the physical body, which ultimately tranlates into works of kindness for others and out in the world. <br/>What color palettes might you prefer? why? love the colors currently chosen<br/>Where will the logo be primarily used? initially business cards, but hopefully future websites, t-shirts, and potentially local magazine adds. Also starting with a small couple of banners for community events in the area. I currently practice as a nomad out of my car :)<br/>Are there any elements you would prefer to see in the logo? Movement. A modern depiction of a human body/figure practicing movement. Hoping to avoid a stereotypical yoga pose per say, just because I want to people to think of it more of a movement practice with yoga roots. Modern yoga. There are elements of breathing and connecting with oneself through the flow of breath and movement, but I do not focus on the meditative/cerebral aspect of the yoga practice. What I teach is almost reaching a meditative state through movement. I personally don't practice, nor resonate with just seated meditation. just not my thing :)<br/>In your opinion, what defines a well-designed logo? curiosity. enough info for individuals to think they know what it means, but want to know more. invokes curiosity, but not too abstract. Reproducible. not too complicated. I want also to invoke a community feel, so a design that appeals to all people within a community. <br/>What is your preference in reference to icons, typography, spokespeople (characters), etc.? modern design. I love the idea of a logo for my purposes, to invoke a sense of movement from within. So not too static. <br/>What words or icons must be included in the logo? movement with yoga roots. <br/>What logos do you like and why? A representation, but not exact. I think some ambiguity is intriguing for others, and also memorable. I want it to be an artistic representation of movement/yoga<br/>What logos do you dislike and why? too busy, too loud. <br/>In your opinion, what is the primary purpose for a logo? association<br/>Who is the primary target audience? (who is most likely to use your services/product?) Children and their parents, but ultimately to expand into teaching adults. I even have aspirations of prenatal and post-natal yoga. Potentially incorporating infants. <br/>Who currently uses your product the most? n/a (working in schools/daycare currently. It is currently all volunteer)<br/>Are you pleased with the range of people your company serves? n/a<br/>Are you looking to expand, modify, or completely change your target audience? or will it remain the same? yes! expand into an adult audience. <br/>How do you plan to focus on your target audience? currently by working through schools and daycares. hopefully ultimately through after school care programs and then offering kid yoga in an existing yoga studio (working on this with Q Studio in Ridgeland, currently)<br/>What are your main forms of advertising? word of mouth, schools, daycares. Happy kids talking to their parents about the yoga class they took and happy teachers :)<br/>How do most customers find out about your company?<br/>Which gender are you targeting? All genders! However, with kid yoga, often the maternal individual in the child's life is more involved with decision making as far as extracurricular activities

Target Market(s)

individuals and families interested in wellness and feeling great

Contact Information for Business Card

Dana Whitford
Yoga Instructor
RYT-200, RCYT

certified yoga teacher for adults and children

Colors

Designer to choose colors to be used in the design.

Requirements
Must have
• "Practice Radiant Movement"
Nice to have
• logo with same colors

```html
<!DOCTYPE html>
<html lang="en">
<head>
<meta charset="utf-8">
<title>Glowline Studios – Business Card</title>
<link rel="stylesheet" href="https://fonts.googleapis.com/css2?family=Lato:wght@400;700;900&display=swap">
<style>
  :root {
    --backdrop: #2a2a2c;
    --card: #1c1c1e;
    --sun: #f5d63b;
    --ink: #f2f2f2;
    --rule: #5a5a5e;
  }
  * { box-sizing: border-box; margin: 0; padding: 0; }
  html, body {
    width: 1200px; height: 1108px; overflow: hidden;
    background: var(--backdrop);
    font-family: "Lato", sans-serif;
    color: var(--ink);
  }
  .stage { position: relative; width: 1200px; height: 1108px; }
  .card {
    position: absolute; top: 244px;
    width: 380px; height: 620px;
    background: var(--card);
    border-radius: 22px;
    box-shadow: 0 18px 40px rgba(0,0,0,.45);
  }
  .card--front { left: 170px; }
  .card--back { left: 650px; }

  .brand { display: flex; justify-content: center; }
  .brand__row { display: flex; align-items: center; gap: 12px; }
  .brand__dot { width: 30px; height: 30px; border-radius: 50%; background: var(--sun); }
  .brand__name { font-weight: 700; font-size: 30px; color: var(--sun); letter-spacing: .5px; }
  .card--front .brand { margin-top: 124px; }

  .person { margin-top: 112px; text-align: center; }
  .person__name { font-weight: 900; font-size: 25px; color: var(--sun); letter-spacing: .5px; }
  .person__role { font-size: 19px; color: var(--ink); margin-top: 2px; }

  .divider { display: flex; align-items: center; gap: 6px; margin: 16px 40px 12px; }
  .divider__line { flex: 1; height: 1px; background: var(--rule); }
  .divider__icon {
    width: 26px; height: 26px; border-radius: 50%; background: var(--sun);
    display: flex; align-items: center; justify-content: center;
  }
  .divider__icon svg { width: 15px; height: 15px; }

  .contact { text-align: center; font-size: 19px; line-height: 1.4; }
  .rule { height: 1px; background: var(--rule); margin: 12px 40px; }
  .address { text-align: center; font-size: 19px; line-height: 1.35; }

  .card--back .brand { position: absolute; top: 286px; left: 0; right: 0; }
  .card--back .brand__name { font-size: 22px; }
  .card--back .brand__dot { width: 22px; height: 22px; }

  .social {
    position: absolute; bottom: 70px; left: 0; right: 0;
    display: flex; justify-content: center; gap: 8px;
  }
  .social__item {
    font-size: 11px; color: var(--ink);
    border: 1.5px solid var(--ink); border-radius: 14px;
    padding: 5px 9px;
  }
</style>
</head>
<body>
<main class="stage">
  <section class="card card--front">
    <div class="brand">
      <div class="brand__row">
        <span class="brand__dot"></span>
        <span class="brand__name">Glowline Studios</span>
      </div>
    </div>

    <div class="person">
      <h1 class="person__name">DANA WHITFORD</h1>
      <p class="person__role">Managing Director</p>
    </div>

    <div class="divider">
      <span class="divider__line"></span>
      <span class="divider__icon">
        <svg viewBox="0 0 16 16" aria-hidden="true"><path d="M4 2l2.5 0 1 3-1.5 1.2a7 7 0 0 0 3.8 3.8L11 8.5l3 1V12a1.5 1.5 0 0 1-1.5 1.5A10.5 10.5 0 0 1 2.5 3.5 1.5 1.5 0 0 1 4 2z" fill="#1c1c1e"/></svg>
      </span>
      <span class="divider__icon">
        <svg viewBox="0 0 16 16" aria-hidden="true"><rect x="2" y="4" width="12" height="8" fill="none" stroke="#1c1c1e" stroke-width="1.6"/><path d="M2 4l6 5 6-5" fill="none" stroke="#1c1c1e" stroke-width="1.6"/></svg>
      </span>
      <span class="divider__icon">
        <svg viewBox="0 0 16 16" aria-hidden="true"><circle cx="8" cy="8" r="6" fill="none" stroke="#1c1c1e" stroke-width="1.5"/><ellipse cx="8" cy="8" rx="2.6" ry="6" fill="none" stroke="#1c1c1e" stroke-width="1.2"/><path d="M2 8h12" stroke="#1c1c1e" stroke-width="1.2"/></svg>
      </span>
      <span class="divider__line"></span>
    </div>

    <div class="contact">
      <p>044-555 010 276</p>
      <p>hello@glowline.com</p>
      <p>www.glowlinestudios.com</p>
    </div>
    <div class="rule"></div>
    <div class="address">
      <p>18 Cedar Row,</p>
      <p>39157, Ridgeland</p>
    </div>
  </section>

  <section class="card card--back">
    <div class="brand">
      <div class="brand__row">
        <span class="brand__dot"></span>
        <span class="brand__name">Glowline Studios</span>
      </div>
    </div>
    <div class="social">
      <span class="social__item">Circle</span>
      <span class="social__item">Chirp</span>
      <span class="social__item">Linkup</span>
      <span class="social__item">Snapshot</span>
    </div>
  </section>
</main>
</body>
</html>
```